we can communicate on this, but i want to follow the approach we took on Pellew|Marsh & Quinlan but i feel the card front needs the black background and the platinum and gold logo. The back? I am open. we can use the same info from PM&Q. Velmont Arc is an enhanced equity investment fund - basically a very exclusive boutique hedge fund that uses only stock options. very advanced things. hope you are interested

Contact Information for Business Card

Dr. Lewis T. Brennick, CFA
Scientifique de fusée financière
701.555.0143
LTBquant47@mailvantor.com

4718 Willow Creek Bend W.
West Fargo, ND 58078

No web site

Colors

Designer to choose colors to be used in the design.

Requirements
Nice to have
• I tend to prefer the most visible applications of the logo to include logo and name, the logo version with a black background and the gold and platinum components separated by the black. I see this working well for a single side (logo and name - this is card front to me).
• I am fairly open to other treatments on the reverse side with the data. To me, it makes sense to have a different color rendition of the logo on the reverse and it may be a muted black tone on tone or an oversized portion that would have spot UV. Or, the reverse may play with colors and layout
Should not have
• Other colors = no no
• Decorative font

```html
<!DOCTYPE html>
<html lang="en">
<head>
<meta charset="utf-8">
<title>Velmont Arc Business Card</title>
<link href="https://fonts.googleapis.com/css2?family=Montserrat:wght@400;500;600;700&display=swap" rel="stylesheet">
<style>
  :root {
    --stage: #a4a4a4;
    --card-dark: #262626;
    --card-light: #ffffff;
    --gold: #c9a227;
    --ink: #1f1f1f;
    --white: #ffffff;
  }
  * { margin: 0; padding: 0; box-sizing: border-box; }
  html, body {
    width: 1200px; height: 930px; overflow: hidden;
    background: radial-gradient(ellipse at 50% 40%, #c2c2c2 0%, var(--stage) 70%, #8e8e8e 100%);
    font-family: "Montserrat", sans-serif;
  }
  .stage { position: relative; width: 1200px; height: 930px; }
  .card {
    position: absolute; width: 560px; height: 320px; border-radius: 22px;
    box-shadow: 0 14px 30px rgba(0,0,0,0.28);
    overflow: hidden;
  }
  .card-front {
    left: 320px; top: 110px; background: var(--card-dark);
    display: flex; align-items: center; justify-content: center; gap: 22px;
  }
  .brand-mark { width: 64px; height: 64px; border-radius: 50%; background: var(--gold); flex: none; }
  .brand-name {
    color: var(--white); font-weight: 700; font-size: 38px; letter-spacing: 1px;
    text-transform: uppercase; line-height: 1; white-space: nowrap;
  }
  .card-back { left: 320px; top: 500px; background: var(--card-light); }
  .back-brand {
    position: absolute; left: 22px; top: 0; width: 196px; height: 320px;
    display: flex; flex-direction: column; align-items: center; justify-content: center; gap: 16px;
  }
  .back-brand .brand-mark { width: 96px; height: 96px; }
  .back-brand .brand-name { color: var(--ink); font-size: 20px; }
  .divider {
    position: absolute; left: 238px; top: 70px; width: 2px; height: 180px; background: var(--gold);
  }
  .details {
    position: absolute; left: 260px; top: 78px; width: 284px;
    color: var(--ink); font-size: 13px; line-height: 1.4; white-space: nowrap;
  }
  .person-name {
    color: var(--gold); font-weight: 600; font-size: 15px; text-transform: uppercase; letter-spacing: 0.2px;
  }
  .person-title { margin-left: 8px; font-size: 13px; margin-bottom: 10px; }
  .address { margin-left: 16px; margin-bottom: 8px; }
  .contact-list { list-style: none; margin-left: 22px; }
  .contact-list li { display: flex; align-items: center; gap: 8px; }
  .contact-list svg { width: 11px; height: 11px; flex: none; }
</style>
</head>
<body>
<main class="stage">
  <section class="card card-front" aria-label="Card front">
    <span class="brand-mark" aria-hidden="true"></span>
    <span class="brand-name">Velmont Arc</span>
  </section>

  <section class="card card-back" aria-label="Card back">
    <div class="back-brand">
      <span class="brand-mark" aria-hidden="true"></span>
      <span class="brand-name">Velmont Arc</span>
    </div>
    <div class="divider"></div>
    <div class="details">
      <p class="person-name">Dr. Lewis T. Brennick, CFA</p>
      <p class="person-title">Scientifique de fusée financière</p>
      <p class="address">4718 Willow Creek Bend W.<br>West Fargo, ND 58078</p>
      <ul class="contact-list">
        <li>
          <svg viewBox="0 0 12 12"><path d="M2 1 L4.5 1 L5.5 3.8 L4 5 Q5 7 7 8 L8.2 6.5 L11 7.5 L11 10 Q6 11 2 6 Q1 4 2 1Z" fill="var(--gold)"/></svg>
          701.555.0143
        </li>
        <li>
          <svg viewBox="0 0 12 12"><rect x="1" y="2.5" width="10" height="7" fill="none" stroke="var(--gold)" stroke-width="1.3"/><path d="M1 2.5 L6 6.5 L11 2.5" fill="none" stroke="var(--gold)" stroke-width="1.3"/></svg>
          LTBquant47@mailvantor.com
        </li>
      </ul>
    </div>
  </section>
</main>
</body>
</html>
```